Bookcover: Ways to Turn Into a Bold Pathfinder

I am publishing a super-low-cost innovation book for €4,99 on Quillmere Open Press to help everyone become a great innovator: young ambitious people without college education nor a big budget. Do you want to help me?

Brief:
Design a book cover 1600 x 2560 pixels for QOP.
Main title: Ways to Turn Into a Bold Pathfinder
Sub title: mindset - insights - skills & tools
Author: Joost ter Brakel
Design: captive, and appealing to everyone
Target Group: young ambitious people without college education

For quillmere please format the height/width ratio of 1.6:1

```html
<!DOCTYPE html>
<html lang="en">
<head>
<meta charset="utf-8">
<title>Ways to Turn Into a Bold Pathfinder — Book Cover</title>
<link rel="stylesheet" href="https://fonts.googleapis.com/css2?family=Bebas+Neue&family=Jost:wght@500;700&family=Poppins:wght@600&display=swap">
<style>
  :root {
    --backdrop: #4f4c4b;
    --paper: #ffffff;
    --ink: #0b0b0b;
    --orange-light: #f2a91b;
    --orange-deep: #f0751a;
    --author-orange: #ee7a1e;
    --sketch-light: #efe2d8;
    --sketch-mid: #a9765a;
    --sketch-dark: #4a1c18;
  }
  * { margin: 0; padding: 0; box-sizing: border-box; }
  html, body {
    width: 839px;
    height: 1200px;
    overflow: hidden;
    background: var(--backdrop);
  }
  .canvas {
    position: relative;
    width: 839px;
    height: 1200px;
  }
  .cover {
    position: absolute;
    left: 148px;
    top: 167px;
    width: 544px;
    height: 871px;
    background: var(--paper);
    text-align: center;
    overflow: hidden;
  }
  .title-lead {
    position: absolute;
    top: 60px;
    left: 0;
    width: 100%;
    font-family: "Jost", sans-serif;
    font-weight: 500;
    font-size: 28px;
    letter-spacing: 0.2em;
    padding-left: 0.2em;
    color: var(--ink);
    line-height: 1;
  }
  .title-key {
    position: absolute;
    top: 80px;
    left: 0;
    width: 100%;
    font-family: "Jost", sans-serif;
    font-weight: 700;
    font-size: 124px;
    letter-spacing: -0.01em;
    color: var(--ink);
    line-height: 1;
  }
  .title-main {
    position: absolute;
    top: 181px;
    left: 0;
    width: 100%;
    font-family: "Bebas Neue", sans-serif;
    font-size: 134px;
    line-height: 1;
    letter-spacing: -0.005em;
    background: linear-gradient(180deg, var(--orange-light) 15%, var(--orange-deep) 85%);
    -webkit-background-clip: text;
    background-clip: text;
    color: transparent;
  }
  .cover-art {
    position: absolute;
    top: 302px;
    left: 0;
    width: 544px;
    height: 444px;
    display: block;
  }
  .subtitle {
    position: absolute;
    top: 764px;
    left: 0;
    width: 100%;
    font-family: "Poppins", sans-serif;
    font-weight: 600;
    font-size: 20px;
    letter-spacing: 0.1em;
    color: var(--ink);
    line-height: 1;
    white-space: nowrap;
  }
  .subtitle .divider { margin: 0 0.6em; }
  .author {
    position: absolute;
    top: 806px;
    left: 0;
    width: 100%;
    font-family: "Bebas Neue", sans-serif;
    font-size: 33px;
    letter-spacing: 0.06em;
    color: var(--author-orange);
    line-height: 1;
  }
</style>
</head>
<body>
<main class="canvas">
  <article class="cover">
    <h1>
      <span class="title-lead">WAYS TO TURN INTO A</span>
      <span class="title-key">BOLD</span>
      <span class="title-main">PATHFINDER</span>
    </h1>

    <svg class="cover-art" viewBox="0 0 544 444" role="img" aria-label="Pen sketch of a light bulb shaped like a mountain rising from the ground, with a small figure standing triumphantly on the peak">
      <defs>
        <linearGradient id="art-body" x1="0" y1="0" x2="0" y2="1">
          <stop offset="0%" stop-color="var(--sketch-light)"/>
          <stop offset="55%" stop-color="var(--sketch-mid)"/>
          <stop offset="100%" stop-color="var(--sketch-dark)"/>
        </linearGradient>
        <linearGradient id="art-ground" x1="0" y1="0" x2="1" y2="0">
          <stop offset="0%" stop-color="var(--sketch-light)" stop-opacity="0"/>
          <stop offset="50%" stop-color="var(--sketch-dark)"/>
          <stop offset="100%" stop-color="var(--sketch-light)" stop-opacity="0"/>
        </linearGradient>
      </defs>
      <rect x="140" y="0" width="264" height="390" rx="120" fill="url(#art-body)" opacity="0.85"/>
      <rect x="0" y="370" width="544" height="60" rx="30" fill="url(#art-ground)" opacity="0.8"/>
    </svg>

    <p class="subtitle">MINDSET<span class="divider">|</span>INSIGHTS<span class="divider">|</span>SKILLS &amp; TOOLS</p>
    <p class="author">JOOST TER BRAKEL</p>
  </article>
</main>
</body>
</html>
```